Web design project for exciting Australian start-up

Background
We are looking for a creative and talented web design artist to work alongside our market leading web developer.
• You will be required to create a modern and clean design theme for our website, incorporating selected rustic colour scheme elements for our exciting Australian start-up to operate within the coffee industry.
reoccurring work to be expected to flow to the successful designer.
Requirements
• c. 5 - 10 page website
• Landing page
• Log in/ out
• 404 template
• Typography is emphasised
• Please use either a) typemarrow.com, b) free web fonts, c) brindle fonts
• All design elements in vector format
• Preferably with icons for each header title(i.e. about us, how it works etc) but designer have free reign over how the site looks, so might not be applicable
• All pages to be responsive
• Down to eSlab resolution

High level visual design brief attached - additional pages to be worked from base design.

Design inspiration
• We would like to use design elements from the following sources:
http://www.zandrix.com/halcyon/ (Functionality)
Colour scheme refer to logo and complementary style guide

```html
<!DOCTYPE html>
<html lang="en">
<head>
<meta charset="utf-8">
<title>Roastwell — Coffee Marketplace</title>
<link rel="stylesheet" href="https://fonts.googleapis.com/css2?family=Open+Sans:wght@300;400;700&family=Roboto+Slab:wght@300;400&display=swap">
<style>
:root{
  --orange:#f89c2b;
  --red:#e53b3b;
  --ink:#222;
  --nav-text:#444;
  --nav-active:#f3f3f3;
  --rule:#ececec;
  --footer-bg:#e8e8e8;
  --footer-text:#555;
  --base-bg:#4b4b4b;
  --base-rule:#6a6a6a;
  --white:#fff;
  --hero-dark:#3e2112;
  --hero-mid:#7a4628;
  --hero-light:#9a6a48;
}
*{box-sizing:border-box;margin:0;padding:0}
html,body{width:1200px;height:950px;overflow:hidden;background:var(--white)}
body{position:relative;font-family:"Roboto Slab",serif}
.site-header{position:absolute;left:0;top:0;width:1200px;height:107px;background:var(--white)}
.brand{position:absolute;left:161px;top:34px;display:flex;align-items:center;gap:12px}
.brand-mark{width:38px;height:38px;border-radius:50%;background:var(--orange)}
.brand-name{font-family:"Open Sans",sans-serif;font-weight:700;font-size:28px;color:var(--ink);letter-spacing:1px}
.main-nav{position:absolute;left:560px;top:0;height:107px;display:flex;border-left:1px solid var(--rule)}
.nav-item{height:107px;display:flex;flex-direction:column;align-items:center;justify-content:center;gap:8px;border-right:1px solid var(--rule);font-family:"Open Sans",sans-serif;font-size:12px;color:var(--nav-text);text-transform:uppercase}
.nav-item.is-active{background:var(--nav-active)}
.nav-item svg{width:20px;height:20px}
.nav-about{width:94px}.nav-how{width:135px}.nav-faq{width:66px}
.auth{position:absolute;top:38px;display:flex;align-items:center;justify-content:center;height:31px;width:76px;color:var(--white);font-family:"Open Sans",sans-serif;font-size:14px;border-radius:2px}
.auth-login{left:878px;background:var(--orange)}
.auth-signup{left:963px;background:var(--red)}
.hero{position:absolute;left:0;top:107px;width:1200px;height:542px;background:linear-gradient(115deg,var(--hero-dark) 0%,var(--hero-mid) 35%,var(--hero-light) 60%,var(--hero-mid) 80%,var(--hero-dark) 100%)}
.hero-title{position:absolute;left:0;width:1200px;text-align:center;color:var(--white);font-family:"Open Sans",sans-serif;line-height:1}
.hero-kicker{top:213px;font-size:22px;font-weight:300}
.hero-headline{top:246px;font-size:36px;font-weight:700}
.hero-cta{position:absolute;left:519px;top:302px;width:162px;height:44px;background:var(--orange);color:var(--white);display:flex;align-items:center;justify-content:center;font-size:18px;font-family:"Open Sans",sans-serif}
.slide-arrow{position:absolute;top:240px;width:56px;height:56px}
.slide-prev{left:161px}.slide-next{left:981px}
.site-footer{position:absolute;left:0;top:649px;width:1200px;height:237px;background:var(--footer-bg)}
.footer-col{position:absolute;top:50px}
.footer-col h3{font-weight:400;font-size:17px;color:var(--ink);letter-spacing:.5px;margin-bottom:14px;font-family:"Roboto Slab",serif}
.footer-col li{list-style:none;font-size:14px;font-weight:300;color:var(--footer-text);height:31px;display:flex;align-items:center;font-family:"Roboto Slab",serif}
.col-info{left:295px}.col-who{left:541px}.col-who li{padding-left:3px}.col-join{left:797px}
.col-join li{padding-left:3px}
.col-join .label{width:76px}
.social-dot{width:10px;height:10px;background:#666}
.base-bar{position:absolute;left:0;top:886px;width:1200px;height:64px;background:var(--base-bg)}
.base-bar::before{content:"";position:absolute;left:161px;top:5px;width:878px;height:1px;background:var(--base-rule)}
.copyright{position:absolute;top:22px;width:1200px;text-align:center;color:var(--white);font-size:14px;font-weight:300;font-family:"Roboto Slab",serif}
</style>
</head>
<body>
<header class="site-header">
  <div class="brand"><span class="brand-name">ROASTWELL</span><span class="brand-mark"></span></div>
  <nav class="main-nav">
    <div class="nav-item nav-about is-active">
      <svg viewBox="0 0 20 20" fill="none" stroke="var(--orange)" stroke-width="1.4"><path d="M2 10 L10 3 L18 10"/><path d="M4.5 8.5 V17 H15.5 V8.5"/><path d="M8.5 17 V12 H11.5 V17"/></svg>
      About Us</div>
    <div class="nav-item nav-how">
      <svg viewBox="0 0 20 20" fill="none" stroke="#777" stroke-width="1.4"><circle cx="8" cy="7" r="3"/><path d="M2 18 C2 13 14 13 14 18"/><rect x="12" y="2" width="6" height="5"/></svg>
      How it works</div>
    <div class="nav-item nav-faq">
      <svg viewBox="0 0 20 20" fill="none" stroke="#777" stroke-width="1.4"><rect x="4" y="4" width="4" height="14"/><rect x="12" y="2" width="4" height="16"/></svg>
      FAQ</div>
  </nav>
  <a class="auth auth-login">Login</a>
  <a class="auth auth-signup">Sign up</a>
</header>

<section class="hero" role="img" aria-label="Photo of roasted coffee beans scattered on a wooden table around a white cup of black coffee">
  <p class="hero-title hero-kicker">AUSTRALIA FIRST ONLINE</p>
  <h1 class="hero-title hero-headline">COFFEE MARKETPLACE</h1>
  <a class="hero-cta">Watch Video</a>
  <svg class="slide-arrow slide-prev" viewBox="0 0 56 56" fill="none" stroke="#fff" stroke-width="2"><circle cx="28" cy="28" r="27"/><path d="M31 22 L25 28 L31 34"/></svg>
  <svg class="slide-arrow slide-next" viewBox="0 0 56 56" fill="none" stroke="#fff" stroke-width="2"><circle cx="28" cy="28" r="27"/><path d="M25 22 L31 28 L25 34"/></svg>
</section>

<footer class="site-footer">
  <div class="footer-col col-info"><h3>HELPFUL INFO</h3><ul><li>About Us</li><li>Media Enquiries</li><li>Terms &amp; Conditions</li><li>Privacy Policy</li></ul></div>
  <div class="footer-col col-who"><h3>WHO WE ARE</h3><ul><li>How it works</li><li>FAQ</li><li>Contact us</li></ul></div>
  <div class="footer-col col-join"><h3>JOIN US ON</h3><ul>
    <li><span class="label">Chatterbook</span><span class="social-dot"></span></li>
    <li><span class="label">Tweetline</span><span class="social-dot"></span></li>
    <li><span class="label">Linkwork</span><span class="social-dot"></span></li>
    <li><span class="label">ClipTube</span><span class="social-dot"></span></li>
  </ul></div>
</footer>
<div class="base-bar"><p class="copyright">Copyright © 2014 Roastwell</p></div>
</body>
</html>
```